A ebook cover to reinvent the imagery of vegetable companion gardening

We needs a ebook design with illustrates minimal as well as clear and concise relevance to vegetable companion gardening . we will add a mock up design and other existing designs to help you gauge and create the sort of illustration fit for our aims.
Book Title: Orchard and Greens 202 – Garden Partner Sowing
Subtitle: Partner Handbook On Raising Crops Through Basic, Natural & Lasting Plot Methods
(Perfect For Beginners)
Author: Amber Hollow
Size: 5.5 x 8.5

```html
<!DOCTYPE html>
<html lang="en">
<head>
<meta charset="utf-8">
<title>Orchard and Greens 202 – Garden Partner Sowing</title>
<link href="https://fonts.googleapis.com/css2?family=Poppins:wght@400;600;700&family=Courgette&display=swap" rel="stylesheet">
<style>
  :root {
    --backdrop: #d4d0d1;
    --paper: #ffffff;
    --orange: #f39200;
    --charcoal: #3b3b3d;
    --leaf: #3f980c;
    --forest: #1f3d12;
    --mint: #b6ee92;
    --ink: #333333;
  }
  * { margin: 0; padding: 0; box-sizing: border-box; }
  html, body { width: 1200px; height: 3069px; overflow: hidden; }
  body { background: var(--backdrop); font-family: "Poppins", sans-serif; position: relative; }

  .cover {
    position: absolute; left: 100px; top: 761px;
    width: 1000px; height: 1547px;
    background: var(--paper);
    box-shadow: 0 10px 40px rgba(0,0,0,0.22);
  }
  .title {
    position: absolute; left: 0; right: 0; top: 120px;
    text-align: center; font-weight: 700; line-height: 0.92;
    letter-spacing: -3px; font-size: 116px;
  }
  .title .line { display: block; }
  .title .orange { color: var(--orange); }
  .title .charcoal { color: var(--charcoal); }
  .title .leaf { color: var(--leaf); }

  .series-band {
    position: absolute; left: 150px; top: 405px; width: 700px; height: 86px;
  }
  .series-band svg { position: absolute; inset: 0; }
  .series-band .series {
    position: absolute; inset: 0; display: flex; align-items: center; justify-content: center;
    font-family: "Courgette", cursive; color: #fff; font-size: 44px;
  }

  .tagline {
    position: absolute; left: 60px; right: 60px; top: 524px;
    text-align: center; color: var(--ink); font-size: 28px; line-height: 1.22;
  }

  .produce-art {
    position: absolute; left: 0; right: 0; top: 640px; height: 560px;
    background: radial-gradient(ellipse at 50% 55%, #c9772e 0%, #b9462f 25%, #7fae3a 52%, #d8efc2 75%, #ffffff 92%);
  }

  .author-band {
    position: absolute; left: 165px; top: 1295px; width: 670px; height: 104px;
  }
  .author-band svg { position: absolute; inset: 0; }
  .author-band .author {
    position: absolute; inset: 0; display: flex; align-items: center; justify-content: center;
    font-weight: 700; font-size: 50px; letter-spacing: 7px; color: var(--forest);
  }
</style>
</head>
<body>
  <main class="cover">
    <h1 class="title">
      <span class="line"><span class="orange">ORCHARD</span> <span class="charcoal">AND</span></span>
      <span class="line"><span class="leaf">GREENS</span> <span class="orange">202</span></span>
    </h1>

    <div class="series-band">
      <svg viewBox="0 0 700 86" preserveAspectRatio="none" aria-hidden="true">
        <polygon points="30,12 680,4 640,22 700,40 650,52 690,70 40,84 60,64 0,48 50,34" fill="var(--forest)"/>
      </svg>
      <p class="series">Garden Partner Sowing</p>
    </div>

    <p class="tagline">Partner Handbook On Raising Crops Through<br>Basic, Natural &amp; Lasting Plot Methods</p>

    <div class="produce-art" role="img" aria-label="Arrangement of fresh vegetables, fruit, grains and herbs with light green line-drawn leaves"></div>

    <div class="author-band">
      <svg viewBox="0 0 670 104" preserveAspectRatio="none" aria-hidden="true">
        <polygon points="0,0 670,0 640,52 670,104 0,104 30,52" fill="var(--mint)"/>
      </svg>
      <p class="author">AMBER HOLLOW</p>
    </div>
  </main>
</body>
</html>
```